Design the Business card for NetVaultic

Business card required for a professional Cyber Security business.
Company Logo and Icon has already been provided however I would like other options for the logo and icon to compare to. Alternatively, please refine/enhance the image of the logo.icon I have already provided.

If you are going to use the provided logo and icon, I was thinking that the company raised Logo on White background would serve well on the front of the card. See attached. AND, a large company raised stand-alone icon to appear on black background on the back of the card with tagline 'Cyber Risk Management, Governance and Consulting' or 'Cyber Security for your Business' See attached.
Alternatively, provide your own design for the logo and icon.

Target Market(s)

Enterprise, Government, Financial.

Contact Information for Business Card

Tavin Orloweth
Founder and CEO

Email Address
Mobile Number
Website URL
LinkedIn URL

Logo Text

NetVaultic - see attached example of logo

Font styles to use
Other font styles liked:
• Berlin Sans FB

Requirements
Must have
• Clean large and bold icon on the back with tagline.
• Horizontal alignment,
Nice to have
• Round edges.
• Raised Logo/Icon
Should not have
• An unprofessional look and feel.

```html
<!DOCTYPE html>
<html lang="en">
<head>
<meta charset="utf-8">
<title>NetVaultic Business Card</title>
<link rel="stylesheet" href="https://fonts.googleapis.com/css2?family=Roboto:wght@400;700&family=Roboto+Condensed:wght@700&family=Signika:wght@400&display=swap">
<style>
  :root {
    --stage: #3a3a3c;
    --card-white: #f1f1f1;
    --card-black: #1a1b1d;
    --card-black-edge: #2c2d30;
    --brand-blue: #0a6fc2;
    --wave-blue: #4b6fc6;
    --logo-blue: #3f6fc0;
    --accent-yellow: #f6b800;
    --white: #ffffff;
  }
  html, body {
    margin: 0;
    padding: 0;
    width: 1200px;
    height: 960px;
    overflow: hidden;
    background: var(--stage);
  }
  .canvas { position: relative; width: 1200px; height: 960px; }
  .card {
    position: absolute;
    width: 600px;
    height: 342px;
    border-radius: 18px;
    overflow: hidden;
    box-sizing: border-box;
    box-shadow: 0 3px 8px rgba(0, 0, 0, 0.45);
  }
  .card-front { left: 322px; top: 108px; background: var(--card-white); }
  .card-back {
    left: 321px;
    top: 494px;
    background: var(--card-black);
    border: 1.5px solid var(--card-black-edge);
  }
  .wave { position: absolute; left: 0; top: 0; }
  .brand {
    position: absolute;
    left: 44px;
    top: 76px;
    display: flex;
    align-items: center;
    gap: 10px;
  }
  .brand-dot {
    width: 62px; height: 62px; border-radius: 50%;
    background: var(--logo-blue);
  }
  .brand-name {
    font-family: "Roboto", sans-serif;
    font-weight: 700;
    font-size: 36px;
    color: var(--logo-blue);
  }
  .identity {
    position: absolute;
    right: 29px;
    top: 186px;
    text-align: right;
  }
  .person-name {
    font-family: "Roboto Condensed", sans-serif;
    font-weight: 700;
    font-size: 22px;
    color: var(--accent-yellow);
    line-height: 26px;
  }
  .person-role {
    font-family: "Roboto", sans-serif;
    font-weight: 700;
    font-size: 14px;
    color: var(--white);
    line-height: 18px;
  }
  .contacts {
    position: absolute;
    right: 29px;
    top: 246px;
    margin: 0; padding: 0;
    list-style: none;
  }
  .contacts li {
    display: flex;
    justify-content: flex-end;
    align-items: center;
    gap: 8px;
    height: 19px;
    font-family: "Roboto", sans-serif;
    font-size: 14px;
    color: var(--white);
  }
  .contacts svg { width: 14px; height: 14px; flex: none; }
  .back-brand {
    position: absolute;
    left: 0; right: 0;
    top: 108px;
    display: flex;
    justify-content: center;
    align-items: center;
    gap: 16px;
  }
  .back-brand .brand-dot { width: 90px; height: 90px; }
  .back-brand .brand-name { font-size: 46px; }
  .tagline {
    position: absolute;
    left: 0; right: 0;
    top: 274px;
    text-align: center;
    font-family: "Signika", sans-serif;
    font-size: 18px;
    color: var(--logo-blue);
  }
  .tagline .highlight { color: var(--accent-yellow); }
</style>
</head>
<body>
<div class="canvas">
  <section class="card card-front">
    <svg class="wave" width="600" height="342" viewBox="0 0 600 342">
      <path d="M0,272 C80,312 160,330 230,316 C330,292 380,124 470,92 C520,76 560,78 600,78 L600,342 L0,342 Z" fill="var(--brand-blue)"/>
      <path d="M19,274 C90,310 160,326 230,312 C330,288 380,120 470,88 C520,72 556,76 582,83" fill="none" stroke="var(--wave-blue)" stroke-width="6"/>
      <path d="M19,278 C90,314 160,330 230,316 C330,292 380,124 470,92 C520,76 556,80 582,87" fill="none" stroke="var(--white)" stroke-width="1.5"/>
      <circle cx="19" cy="274" r="9" fill="var(--wave-blue)" stroke="var(--white)" stroke-width="2"/>
      <circle cx="582" cy="83" r="9" fill="var(--wave-blue)" stroke="var(--white)" stroke-width="2"/>
    </svg>
    <div class="brand">
      <span class="brand-dot"></span>
      <span class="brand-name">NetVaultic</span>
    </div>
    <div class="identity">
      <div class="person-name">TAVIN ORLOWETH</div>
      <div class="person-role">FOUNDER &amp; CEO</div>
    </div>
    <ul class="contacts">
      <li>555 014 2938
        <svg viewBox="0 0 14 14"><rect x="3.5" y="0.5" width="7" height="13" rx="1.5" fill="none" stroke="var(--accent-yellow)" stroke-width="1.5"/><circle cx="7" cy="11" r="0.9" fill="var(--accent-yellow)"/></svg>
      </li>
      <li>tavin@netvaultic.com
        <svg viewBox="0 0 14 14"><rect x="0.5" y="3" width="13" height="8.5" fill="var(--accent-yellow)"/><path d="M0.5,3 L7,8 L13.5,3" fill="none" stroke="var(--brand-blue)" stroke-width="1"/></svg>
      </li>
      <li>www.netvaultic.com
        <svg viewBox="0 0 14 14"><circle cx="7" cy="7" r="6.5" fill="var(--accent-yellow)"/><path d="M4,4 Q7,6 6,9 M8,3 Q10,5 10,8" fill="none" stroke="var(--brand-blue)" stroke-width="1.2"/></svg>
      </li>
      <li>netvaultic
        <svg viewBox="0 0 14 14"><circle cx="7" cy="7" r="6.5" fill="var(--accent-yellow)"/></svg>
      </li>
    </ul>
  </section>

  <section class="card card-back">
    <div class="back-brand">
      <span class="brand-dot"></span>
      <span class="brand-name">NetVaultic</span>
    </div>
    <div class="tagline">Cyber Risk Management, <span class="highlight">Governance &amp; Consulting</span></div>
  </section>
</div>
</body>
</html>
```